Local Chiropractor Needs Up Scale Webdesign

This website needs to have an upscale look with a very modern feel. Below is the information and websites to reference

Add Logo that is attached

Build a color scheme similar to this website image titled "chiro-1"

Must Include these pages in a horizontal menu bar in this order:
Home, Meet Our Staff, Patient Testimonials, Videos, Work Place Wellness, Contact

Build a "classy looking" Make An Appointment Button into the header with the contact info below

Phone Number:
555-314-2719

Address:
3168 Pelham Orchard Lane, #240
Larkmoor, MN 55490

This website needs 4 rotating banners. Please reference a layout similar to this for the banners: http://drmorlatz.example/. However design it nicer than this website, this website is very boring and doesn't flow with the colors properly

Below are the description for each banner

Rotating Banner #1
Use Image: Pediatrics
Two lines of text. First line title line, second description. Use Latin text for fill

Rotating Banner #2
Use Image: Aging Gracefully

Rotating Banner #3
Use Image: Pregnancy

Rotating Banner #4
Use Image: Athletics

I'd like to see a free consultation box similar to the "chiro-1" image. Fields to include are: First Name, Last Name, Phone Number, Comments.

For the body, please fill it with latin text. Please design a professional body layout. You can include a box in the right column for the hours

Office Hours
Monday: 8:00-11:00, 2:00-5:00
Tuesday: 8:30-11:00, 2:00-5:30
Wednesday: 8:00-11:00, 2:00-5:00
Thursday: 10:00-12:00, 2:30-5:00
Friday: 8:00-10:00, 1:00-5:00
Saturday: Closed
Sunday: Closed

For the footer please design something similar to the: http://drmorlatz.example/

Also include in the Footer: Powered by Brightline Site Works

```html
<!DOCTYPE html>
<html lang="en">
<head>
<meta charset="utf-8">
<title>Verdant Path Chiropractic Health Center</title>
<link rel="stylesheet" href="https://fonts.googleapis.com/css2?family=EB+Garamond:ital,wght@0,400;1,400&family=Mulish:wght@400;600&display=swap">
<style>
:root{
  --header-bg:#1f1f1f;
  --nav-bg:#050505;
  --gold:#c58e1c;
  --gold-line:#8a6a24;
  --brand-green:#9cc23a;
  --deep-green:#2f6b2a;
  --frame-green:#3f7a3c;
  --ink:#1a1a1a;
  --light:#f2f2f2;
  --footer-bg:#232323;
  --footer-base:#1c1c1c;
}
*{margin:0;padding:0;box-sizing:border-box}
html,body{width:695px;height:1200px;overflow:hidden;background:#fff}
body{font-family:"Mulish",sans-serif;color:var(--ink);position:relative}
.abs{position:absolute}

.site-header{left:0;top:0;width:695px;height:66px;background:var(--header-bg)}
.brand{left:16px;top:18px;display:flex;align-items:center;gap:8px;color:var(--brand-green);font-size:15px;font-weight:600;line-height:1.05}
.brand-dot{width:22px;height:22px;border-radius:50%;background:var(--brand-green)}
.brand small{display:block;font-size:9px;font-weight:600}
.header-address{left:215px;top:32px;color:var(--light);font-size:9px;line-height:14px;letter-spacing:0}
.header-phone{left:372px;top:31px;color:var(--light);font-size:11.5px;letter-spacing:.4px;white-space:nowrap}
.header-phone span{font-size:7.5px;margin-right:4px}
.header-divider{left:536px;top:17px;width:2px;height:34px;background:#ddd}
.appointment-btn{left:543px;top:21px;width:120px;height:26px;background:var(--gold);color:#fff;font-size:8.5px;font-weight:600;letter-spacing:.6px;text-align:center;line-height:26px;text-transform:uppercase;text-decoration:none}

.main-nav{left:0;top:66px;width:695px;height:52px;background:var(--nav-bg);border-bottom:2px solid var(--gold-line)}
.main-nav a{position:absolute;top:20px;font-size:9.5px;letter-spacing:.8px;color:#e8e8e8;text-decoration:none;text-transform:uppercase;padding:0 5px;border-left:1px solid #777;border-right:1px solid #777;line-height:13px}
.main-nav a.active{color:var(--brand-green)}

.hero-rule{left:0;top:122px;width:695px;height:20px;background:#fff;border-top:1px solid #ddd;border-bottom:2px solid #d5d5d5}
.hero{left:0;top:142px;width:695px;height:408px;background:linear-gradient(100deg,#cfe1c0 0%,#f3efe6 35%,#f2d7c6 60%,#b9cf78 100%)}
.hero-strip{left:0;top:122px;width:18px;height:428px;background:linear-gradient(#3f4a35,#2c3126)}
.hero-arrow{top:350px}
.caption-title{left:295px;top:412px;width:330px;height:50px;background:rgba(255,255,255,.78);color:var(--deep-green);font-family:"EB Garamond",serif;font-size:35px;letter-spacing:2px;text-align:center;line-height:50px}
.caption-text{left:30px;top:469px;width:635px;height:54px;background:rgba(255,255,255,.72);color:var(--deep-green);font-family:"EB Garamond",serif;font-style:italic;font-size:21.5px;line-height:54px;padding-left:10px}
.hero-base{left:0;top:550px;width:695px;height:5px;border-top:2px solid #d5d5d5}

.intro-title{left:58px;top:594px;font-size:20px;font-weight:400}
.intro-text{left:40px;top:645px;width:319px;font-size:14px;line-height:19.5px;text-align:justify;letter-spacing:.55px}

.hours-card{left:427px;top:578px;width:253px;height:356px;border:1px solid var(--frame-green);padding:5px}
.hours-inner{width:100%;height:100%;border:1px solid var(--frame-green);padding:22px 0 0 17px}
.hours-inner h2{font-size:16px;font-weight:400;margin-bottom:12px}
.hours-inner p{font-size:13px;line-height:39px;height:39px}
.hours-inner b{font-weight:600}

.site-footer{left:0;top:963px;width:695px;height:205px;background:var(--footer-bg);color:var(--light)}
.footer-heading{display:inline-block;font-weight:400;font-size:12px;letter-spacing:1.5px;text-transform:uppercase;padding-bottom:3px;border-bottom:1px solid #888;margin-bottom:10px}
.footer-contact{left:26px;top:28px;font-size:11px;letter-spacing:.6px;line-height:19px}
.footer-contact .num{font-size:14px;margin-left:4px}
.footer-contact .label{font-size:10px}
.footer-contact .addr{font-size:12px}
.map{left:282px;top:32px;width:139px;height:139px;background:linear-gradient(135deg,#e9e2c9,#d8d3b6 60%,#b8cfe0)}
.footer-hours{left:490px;top:28px;font-size:9.5px;letter-spacing:.8px;line-height:19px}
.footer-base{left:0;top:1168px;width:695px;height:32px;background:var(--footer-base);border-top:1px solid #444;color:#bbb;font-size:8px;letter-spacing:.4px;padding:10px 0 0 24px}
</style>
</head>
<body>
<header class="site-header abs">
  <div class="brand abs"><span class="brand-dot"></span><span>Verdant Path<small>Chiropractic Health Center</small></span></div>
  <div class="header-address abs">3168 Pelham Orchard Lane, #240<br>Larkmoor, MN 55490</div>
  <div class="header-phone abs"><span>Phone number:</span>555-314-2719</div>
  <div class="header-divider abs"></div>
  <a class="appointment-btn abs" href="#">Make an Apointment</a>
</header>

<nav class="main-nav abs">
  <a class="active" style="left:32px">Home</a>
  <a style="left:98px">Meet Our Staff</a>
  <a style="left:220px">Patient Testemonials</a>
  <a style="left:377px">Videos</a>
  <a style="left:451px">Work Place Wellness</a>
  <a style="left:604px">Contact</a>
</nav>

<div class="hero-rule abs"></div>
<div class="hero abs" role="img" aria-label="Banner photo: smiling mother holding her toddler outdoors in a sunny green meadow"></div>
<div class="hero-strip abs" role="img" aria-label="Dark textured side strip"></div>
<svg class="hero-arrow abs" style="left:6px" width="14" height="52" viewBox="0 0 14 52"><polyline points="12,2 2,26 12,50" fill="none" stroke="#5b5b5b" stroke-width="2"/></svg>
<svg class="hero-arrow abs" style="left:667px" width="20" height="52" viewBox="0 0 20 52"><polyline points="3,2 17,26 3,50" fill="none" stroke="#4e4e4e" stroke-width="2"/></svg>
<div class="caption-title abs">— PEDIATRICS —</div>
<div class="caption-text abs">”Lorem ipsum dolor sit amet, consectetur adipiscing elit sed do ...”</div>
<div class="hero-base abs"></div>

<main>
  <h1 class="intro-title abs">Lorem ipsum dolor sit amet</h1>
  <p class="intro-text abs">Lorem ipsum dolor sit amet, consectetur adipiscing elit. Integer nec odio. Praesent libero. Sed cursus ante dapibus diam. Sed nisi. Nulla quis sem at nibh elementum imperdiet. Duis sagittis ipsum. Praesent mauris. Fusce nec tellus sed augue semper porta. Mauris massa. Vestibulum lacinia arcu eget nulla. Class aptent taciti sociosqu ad litora torquent per conubia nostra, per inceptos himenaeos. Curabitur sodales porttitor. Morbi lectus risus, iaculis vel, suscipit quis, luctus non, massa. Fusce ac turpis quis ullamcorper.</p>

  <aside class="hours-card abs">
    <div class="hours-inner">
      <h2>Office Hours</h2>
      <p><b>Monday:</b> 8:00-11:00, 2:00-5:00</p>
      <p><b>Tuesday:</b> 8:30-11:00, 2:00-5:30</p>
      <p><b>Wednesday:</b> 8:00-11:00, 2:00-5:00</p>
      <p><b>Thursday:</b> 10:00-12:00, 2:30-5:00</p>
      <p><b>Friday:</b> 8:00-10:00, 1:00-5:00</p>
      <p><b>Saturday:</b> Closed</p>
      <p><b>Sunday:</b> Closed</p>
    </div>
  </aside>
</main>

<footer class="site-footer abs">
  <div class="footer-contact abs">
    <h3 class="footer-heading">Contact</h3>
    <div>Phone number: <span class="num">555-314-2719</span></div>
    <div class="label">Adress:</div>
    <div class="addr">3168 Pelham Orchard Lane, #240<br>Larkmoor, MN 55490</div>
  </div>
  <div class="map abs" role="img" aria-label="Street map showing the office location with a marker pin"></div>
  <div class="footer-hours abs">
    <h3 class="footer-heading">Office Hours</h3>
    <div>Monday: 8:00-11:00, 2:00-5:00</div>
    <div>Tuesday: 8:30-11:00, 2:00-5:30</div>
    <div>Wednesday: 8:00-11:00, 2:00-5:00</div>
    <div>Thursday: 10:00-12:00, 2:30-5:00</div>
    <div>Friday: 8:00-10:00, 1:00-5:00</div>
    <div>Saturday: Closed</div>
    <div>Sunday: Closed</div>
  </div>
</footer>
<div class="footer-base abs">Powered by Brightline Site Works</div>
</body>
</html>
```